interior designer/stylist looking for a letter press business card to reflect the stylish work

Hello Designers,
I need a business card design for an company called Mosaic Interior Design. I'm aiming at the high end residential and private client market in London providing sleek simple interiors. I'd like my business card to be pinterest worthy and expensive looking, i want people to pin it and for it to have a sought after look, and want prospective customers to hire me as their interior designer as my card is so beautiful.
I love letter press design. I also like the use of colour/foil on the edge.
Colour combos & general things I like -
Black and White
Navy Blue and Gold
Neutral colours (muted palette of greys whites navys beiges)
White Marble & brass
Vorelle (fashion designer)
....also open to other suggestions....
Please dont take the pink in the attached photos too literally. i'd like the card to look more masculine than feminine.
I'd like Mosaic on one side in one font, with interior design underneath so one word will make the statement....... unless anyone has any other ideas, open to suggestions.
I'd like a really simple font and for the whole card to look very graphic.
my details -
Petra Wendlecombe
Interior Designer & Stylist
email petra@mosaicinteriordesign.co.uk
phone +447311584209
website wwww.mosaicinteriordesign.co.uk
GO GO GO!! EXCITED TO SEE THE OUTCOME!!
x P
Target Market(s)
High End Residential and private clients
Industry/Entity Type
Business
Contact Information for Business Card
Mosaic Interior Design & Styling
Petra Wendlecombe
phone +447311584209

```html
<!DOCTYPE html>
<html lang="en">
<head>
<meta charset="utf-8">
<title>Mosaic Interior Design – Business Card</title>
<link href="https://fonts.googleapis.com/css2?family=Open+Sans:wght@400;600;700&display=swap" rel="stylesheet">
<style>
  :root {
    --backdrop: #e6e6e8;
    --paper: #f4f4f4;
    --navy: #111733;
    --navy-soft: #1c2347;
    --silver: #e9eaee;
    --ink: #1a1f3a;
  }
  * { box-sizing: border-box; margin: 0; padding: 0; }
  html, body {
    width: 1200px;
    height: 900px;
    overflow: hidden;
    background: var(--backdrop);
    font-family: "Open Sans", Arial, sans-serif;
  }
  .stage {
    width: 1200px;
    height: 900px;
    display: flex;
    align-items: center;
    justify-content: center;
    gap: 40px;
  }
  .card {
    position: relative;
    width: 520px;
    height: 300px;
    border-radius: 22px;
    box-shadow: 0 6px 18px rgba(0, 0, 0, 0.18);
  }

  /* Front */
  .card-front { background: var(--paper); color: var(--ink); }
  .front-wordmark {
    position: absolute;
    top: 34px;
    right: 34px;
    text-align: right;
    color: var(--navy);
    font-weight: 700;
    line-height: 1;
  }
  .front-wordmark .name-word { font-size: 60px; letter-spacing: 2px; display: block; }
  .front-wordmark .tagline { font-size: 23px; letter-spacing: 0.5px; display: block; margin-top: 4px; }

  .person {
    position: absolute;
    left: 36px;
    bottom: 58px;
  }
  .person-name { font-size: 18px; font-weight: 600; color: var(--navy); }
  .person-role { font-size: 12.5px; margin-top: 4px; }

  .contact-list {
    position: absolute;
    right: 30px;
    bottom: 62px;
    list-style: none;
    text-align: right;
    font-size: 12.5px;
  }
  .contact-list li {
    display: flex;
    align-items: center;
    justify-content: flex-end;
    gap: 8px;
    height: 22px;
  }
  .contact-icon { width: 14px; height: 14px; flex: none; }

  /* Back */
  .card-back {
    background: var(--navy);
    display: flex;
    flex-direction: column;
    align-items: center;
    justify-content: center;
    color: var(--silver);
    font-weight: 700;
    line-height: 1;
  }
  .back-wordmark { text-align: center; }
  .back-wordmark .name-word { font-size: 58px; letter-spacing: 3px; display: block; }
  .back-wordmark .tagline { font-size: 16px; letter-spacing: 5px; display: block; margin-top: 10px; }
</style>
</head>
<body>
<main class="stage">
  <section class="card card-front" aria-label="Business card front">
    <div class="front-wordmark">
      <span class="name-word">MOSAIC</span>
      <span class="tagline">INTERIOR DESIGN</span>
    </div>

    <div class="person">
      <p class="person-name">Petra Wendlecombe</p>
      <p class="person-role">Interior Designer &amp; Stylist</p>
    </div>

    <ul class="contact-list">
      <li>+447311584209
        <svg class="contact-icon" viewBox="0 0 14 14" aria-hidden="true">
          <rect width="14" height="14" rx="2" fill="var(--navy)"/>
          <path d="M4 3.2h1.6l.8 2-1 .7a5 5 0 0 0 2.7 2.7l.7-1 2 .8v1.6c0 .5-.4.8-.9.8A7 7 0 0 1 3.2 4.1c0-.5.3-.9.8-.9z" fill="#fff"/>
        </svg>
      </li>
      <li>petra@mosaicinteriordesign.co.uk
        <svg class="contact-icon" viewBox="0 0 14 14" aria-hidden="true">
          <rect width="14" height="14" rx="2" fill="var(--navy)"/>
          <rect x="3" y="4.2" width="8" height="5.6" fill="none" stroke="#fff" stroke-width="1"/>
          <path d="M3 4.4l4 3 4-3" fill="none" stroke="#fff" stroke-width="1"/>
        </svg>
      </li>
      <li>wwww.mosaicinteriordesign.co.uk
        <svg class="contact-icon" viewBox="0 0 14 14" aria-hidden="true">
          <rect width="14" height="14" rx="2" fill="var(--navy)"/>
          <path d="M6 8l2-2M5.2 6.8L4 8a1.4 1.4 0 0 0 2 2l1.2-1.2M8.8 7.2L10 6a1.4 1.4 0 0 0-2-2L6.8 5.2" fill="none" stroke="#fff" stroke-width="1" stroke-linecap="round"/>
        </svg>
      </li>
    </ul>
  </section>

  <section class="card card-back" aria-label="Business card back">
    <div class="back-wordmark">
      <span class="name-word">MOSAIC</span>
      <span class="tagline">INTERIOR DESIGN</span>
    </div>
  </section>
</main>
</body>
</html>
```